SnackOrbit!!! A Vending Machine Business Looking for an attractive website.

We are a vending machine business in Northern Michigan. We have changed our name and have rebranded our company. We would like an attractive website that shares who we are, what services we provide, the products we offer in our machines, along with a form businesses can fill out to see if they are a good fit for our company. I would like to have a Home Page, About SnackOrbit, Why Choose SnackOrbit?, Products & Services, Contact Us (With a Login Option), and a page with a questionnaire for thos interested in getting a FREE Vending Machine.

Target Market(s)

Businesses, Campgrounds, Schools, and many more in Northern Michigan

Industry/Entity Type

Vending Machines

Coding

Coded - Design and coding required

Number of Pages Required

5+ page

Requirements
Must have
• An inviting and enticing Home Page. I want to get my potential clients engaged in our website.
Nice to have
• Possibly background photos from Northern Michigan
Should not have
• A corporate feel. I do not want a boring website.

```html
<!DOCTYPE html>
<html lang="en">
<head>
<meta charset="utf-8">
<title>SnackOrbit – Crave. Vend. Repeat.</title>
<link href="https://fonts.googleapis.com/css2?family=Poppins:wght@400;500;600;700&family=Gelasio:wght@600;700&display=swap" rel="stylesheet">
<style>
:root{
  --purple:#2a2160;
  --purple-dark:#221a52;
  --green:#355e30;
  --green-dark:#2d5228;
  --ink:#111111;
  --muted:#555555;
  --white:#ffffff;
  --line:#d6d6d6;
  --serif:'Gelasio', Georgia, serif;
  --sans:'Poppins', Arial, sans-serif;
}
*{margin:0;padding:0;box-sizing:border-box}
html,body{width:1200px;height:3868px;overflow:hidden}
body{font-family:var(--sans);color:var(--ink);background:var(--white);position:relative}
section,header,footer{position:absolute;left:0;width:1200px}
.abs{position:absolute}
.btn{position:absolute;display:flex;align-items:center;justify-content:center;border-radius:8px;color:var(--white);font-size:12px;font-weight:600}
.btn-green{background:var(--green)}
.btn-purple{background:var(--purple)}
.brand{font-family:var(--serif);font-weight:700;color:var(--purple);display:flex;align-items:center;gap:8px}
.brand .dot{width:14px;height:14px;border-radius:50%;background:var(--green)}
.serif{font-family:var(--serif);font-weight:700}
.hl{color:var(--green)}

/* header */
.site-header{top:0;height:86px;background:var(--white)}
.site-header .brand{left:105px;top:22px;font-size:34px}
.nav{position:absolute;left:392px;top:34px;display:flex;gap:32px;font-size:13px;color:#222}
.site-header .btn{top:26px;height:35px;border-radius:18px;font-weight:500}

/* hero */
.hero{top:86px;height:544px;background:
  radial-gradient(ellipse 170px 260px at 61% 58%, rgba(214,120,214,.85), rgba(160,70,170,.45) 55%, transparent 80%),
  radial-gradient(ellipse 90px 120px at 62% 30%, rgba(150,90,60,.7), transparent 75%),
  radial-gradient(ellipse 200px 300px at 92% 40%, rgba(215,30,50,.95), rgba(140,20,35,.6) 55%, transparent 85%),
  radial-gradient(ellipse 120px 160px at 84% 35%, rgba(230,220,240,.45), transparent 80%),
  radial-gradient(circle 30px at 38% 6%, rgba(200,200,200,.25), transparent 90%),
  radial-gradient(circle 22px at 33% 14%, rgba(200,200,200,.2), transparent 90%),
  linear-gradient(180deg, transparent 70%, rgba(60,50,60,.6) 100%),
  linear-gradient(90deg,#030303 0%,#0c0a10 38%,#3a2040 55%,#4a1a30 75%,#3a0c14 100%)}
.hero h1{position:absolute;left:105px;top:152px;font-size:46px;line-height:56px;font-weight:700;color:var(--white)}
.hero p{position:absolute;left:105px;top:278px;font-size:17px;color:var(--white);font-weight:500}
.hero .btn{left:105px;top:328px;width:142px;height:40px;border-radius:20px;font-size:13px;font-weight:500}

/* about */
.about{top:630px;height:570px}
.about-photo{position:absolute;left:152px;top:80px;width:418px;height:418px;border-radius:50%;background:
  radial-gradient(ellipse 60px 120px at 48% 55%, rgba(245,240,235,.95), transparent 80%),
  radial-gradient(ellipse 70px 150px at 28% 45%, rgba(200,90,60,.75), rgba(60,90,160,.5) 60%, transparent 85%),
  radial-gradient(ellipse 80px 170px at 67% 45%, rgba(230,150,60,.55), transparent 80%),
  radial-gradient(ellipse 60px 80px at 12% 70%, rgba(40,40,40,.8), transparent 85%),
  linear-gradient(90deg,#8a8f96 0%,#d8dade 45%,#f2f2f2 75%,#b8bcc2 100%);border:6px solid var(--green);border-top-color:transparent;border-right-color:transparent}
.about .eyebrow{position:absolute;left:643px;top:142px;font-size:16px;color:var(--green)}
.about .brand{position:absolute;left:638px;top:180px;font-size:40px}
.about p{position:absolute;left:638px;top:255px;width:424px;font-size:11.5px;line-height:23px;letter-spacing:.4px;color:#222}
.about .btn{left:638px;top:385px;width:124px;height:37px}

/* products */
.products{top:1200px;height:755px}
.product{position:absolute;top:0;width:600px;height:755px;text-align:center;color:var(--white)}
.product.left{left:0;background:var(--purple)}
.product.right{left:600px;background:var(--green)}
.machine{position:absolute;left:250px;top:92px;width:245px;height:415px;border:4px solid #cfcfcf;background:
  linear-gradient(180deg,#202020 0%,#8a6a6a 12%,#6f7fa0 30%,#9a7060 48%,#6a7a90 66%,#3a3a3a 80%,#1a1a1a 100%)}
.product.right .machine{left:122px;width:210px;border-color:#e0e0e0;background:
  linear-gradient(180deg,#161616 0%,#8a5a4a 15%,#a04030 30%,#3a4a7a 50%,#5a7090 62%,#b03030 78%,#1a1a2a 100%)}
.product h3{position:absolute;top:518px;width:100%;font-size:27px}
.product.left h3{left:70px}
.product.right h3{left:-72px}
.product p{position:absolute;top:562px;width:400px;font-size:11.5px;line-height:23px}
.product.left p{left:170px}
.product.right p{left:28px}
.product .btn{top:645px;width:124px;height:34px}
.product.left .btn{left:309px}
.product.right .btn{left:167px}

/* why */
.why{top:1955px;height:653px}
.why h2{position:absolute;top:78px;width:100%;text-align:center;font-size:41px}
.why .ring{position:absolute;left:408px;top:167px;width:376px;height:376px;border-radius:50%;border:2px dashed var(--line)}
.why .core{position:absolute;left:486px;top:224px;width:228px;height:228px;border-radius:50%;background:var(--white);box-shadow:0 4px 18px rgba(0,0,0,.1);display:flex;align-items:center;justify-content:center}
.why .core .brand{font-size:34px}
.icon{position:absolute;width:78px;height:78px;border-radius:50%;display:flex;align-items:center;justify-content:center}
.icon.p{background:var(--purple)}
.icon.g{background:var(--green)}
.feat{position:absolute;width:228px}
.feat h4{font-family:var(--serif);font-size:16px;margin-bottom:12px}
.feat p{font-size:10px;line-height:19px;letter-spacing:.5px;color:var(--muted)}
.feat.l{left:144px;text-align:right}
.feat.r{left:826px}

/* testimonials */
.clients{top:2608px;height:500px;background:var(--green)}
.clients h2{position:absolute;top:90px;width:100%;text-align:center;font-size:41px;color:var(--white)}
.card{position:absolute;top:184px;width:445px;height:160px;background:var(--white);border-radius:6px}
.card::after{content:"";position:absolute;left:70px;bottom:-12px;border:12px solid transparent;border-bottom:0;border-top-color:var(--white)}
.card .q{position:absolute;font-family:Georgia,serif;font-weight:700;font-size:110px;color:#a19fae;line-height:1;height:60px}
.card .q.open{left:18px;top:2px}
.card .q.close{right:128px;top:94px}
.card p{position:absolute;left:76px;top:38px;width:345px;font-size:11.5px;line-height:22px;color:#222}
.person{position:absolute;top:2972px;display:flex;align-items:center;gap:12px;color:var(--white);font-family:var(--serif);font-weight:700;font-size:16px}
.avatar{width:50px;height:50px;border-radius:50%;background:radial-gradient(circle at 50% 40%,#c9a890,#6a5a50);border:3px solid var(--white)}
.arrow{position:absolute;width:36px;height:36px;border-radius:50%;display:flex;align-items:center;justify-content:center}

/* cta */
.cta{top:3108px;height:390px;text-align:center}
.cta h2{position:absolute;top:92px;width:100%;font-size:40px;line-height:50px}
.cta p{position:absolute;top:196px;width:100%;font-size:14px;line-height:27px;font-weight:500}
.cta .btn{left:544px;top:264px;width:112px;height:38px}

/* footer */
.site-footer{top:3498px;height:370px;background:var(--purple);color:var(--white)}
.site-footer h5{font-family:var(--serif);font-size:18px;margin-bottom:14px}
.links{position:absolute;left:144px;top:82px}
.links li{list-style:none;font-size:12px;line-height:30px}
.links li::before{content:"▸";font-size:9px;margin-right:6px}
.site-footer .brand{position:absolute;left:430px;top:130px;font-size:56px;color:var(--white)}
.site-footer .brand .dot{width:22px;height:22px}
.social{position:absolute;left:517px;top:226px;display:flex;gap:6px}
.social span{width:29px;height:29px;border-radius:50%;border:2px solid var(--white)}
.contact{position:absolute;left:868px;top:82px}
.contact .row{display:flex;gap:12px;margin-bottom:20px;font-size:11.5px;line-height:18px}
.bottom-bar{position:absolute;left:0;top:312px;width:1200px;height:58px;background:var(--green);text-align:center;line-height:58px;font-family:var(--serif);font-size:13px;font-weight:600}
</style>
</head>
<body>

<header class="site-header">
  <div class="brand abs"><span class="dot"></span>SnackOrbit</div>
  <nav class="nav"><span>Home</span><span>About SnackOrbit</span><span>Why Choose Us?</span><span>Products &amp; Services</span></nav>
  <a class="btn btn-green" style="left:912px;width:106px">Contact Us</a>
  <a class="btn btn-purple" style="left:1023px;width:72px">Login</a>
</header>

<section class="hero" role="img" aria-label="Night photo of a woman in a pink floral kimono looking at a glowing red drinks vending machine">
  <h1>SnackOrbit: Crave.<br>Vend. Repeat.</h1>
  <p>Elevating Snacking, One Vend at a Time</p>
  <a class="btn btn-green">Contact Us &nbsp;➔</a>
</section>

<section class="about">
  <div class="about-photo" role="img" aria-label="Round photo of a customer choosing a snack from a vending machine"></div>
  <div class="eyebrow serif">About</div>
  <div class="brand"><span class="dot"></span>SnackOrbit</div>
  <p>At SnackOrbit, we don't just vend snacks—we curate cravings. Our customized vending solutions bring flavor, convenience, and community to Northern Michigan. Whether you're reaching for a <b>mid-morning snack</b>, a <b>refreshing beverage</b>, or a <b>satisfying breakfast burrito</b>, SnackOrbit delivers delight with every bite</p>
  <a class="btn btn-purple">Contact Us</a>
</section>

<section class="products">
  <div class="product left">
    <div class="machine" role="img" aria-label="Snack vending machine stocked with rows of chips and candy"></div>
    <h3 class="serif">Vending Machine - 1</h3>
    <p>Lorem ipsum dolor sit amet, consectetuer adipiscing elit, sed diam nonummy nibh euismod tincidunt ut laoreet dolore magna aliquam erat volutpat. Ut wisi enim ad minim veniam.</p>
    <a class="btn btn-green">View Details</a>
  </div>
  <div class="product right">
    <div class="machine" role="img" aria-label="Combo vending machine stocked with snacks, bottled water and sodas"></div>
    <h3 class="serif">Vending Machine - 2</h3>
    <p>Lorem ipsum dolor sit amet, consectetuer adipiscing elit, sed diam nonummy nibh euismod tincidunt ut laoreet dolore magna aliquam erat volutpat. Ut wisi enim ad minim veniam.</p>
    <a class="btn btn-purple">View Details</a>
  </div>
</section>

<section class="why">
  <h2 class="serif">Why Choose <span class="hl">SnackOrbit</span></h2>
  <div class="ring"></div>
  <div class="core"><div class="brand"><span class="dot"></span>SnackOrbit</div></div>

  <div class="icon p" style="left:394px;top:216px"><svg width="34" height="34" viewBox="0 0 24 24" fill="none" stroke="#fff" stroke-width="1.4"><path d="M12 22s7-7 7-12a7 7 0 0 0-14 0c0 5 7 12 7 12z"/><path d="M12 14l-3-3a2 2 0 0 1 3-2.5A2 2 0 0 1 15 11z"/></svg></div>
  <div class="icon g" style="left:723px;top:216px"><svg width="34" height="34" viewBox="0 0 24 24" fill="none" stroke="#fff" stroke-width="1.4"><path d="M6 20v-7h3l3-5 1 1v4h5l-1 7z"/><circle cx="8" cy="5" r="1.5"/><circle cx="16" cy="5" r="1.5"/></svg></div>
  <div class="icon g" style="left:394px;top:421px"><svg width="34" height="34" viewBox="0 0 24 24" fill="none" stroke="#fff" stroke-width="1.4"><circle cx="9" cy="9" r="6"/><circle cx="16" cy="15" r="5"/></svg></div>
  <div class="icon p" style="left:723px;top:421px"><svg width="34" height="34" viewBox="0 0 24 24" fill="none" stroke="#fff" stroke-width="1.4"><path d="M4 20h16M6 20v-5M10 20v-8M14 20v-6M18 20v-10"/><path d="M5 11l5-4 4 3 5-6"/></svg></div>

  <div class="feat l" style="top:190px"><h4>Local Love</h4><p>We celebrate the heart of Michigan by partnering with local legends. Say hello to Pine Ridge Jerky and North Shore Potato Chips—our hometown heroes. Their flavorsdance on your taste buds, and we're thrilled to bring them straight to your workplace.</p></div>
  <div class="feat l" style="top:397px"><h4>Unleash Your Cravings</h4><p style="text-align:left">SnackOrbit isn't bound by corporate ties. We're the rebels of the vending world. Craving a bag of crispy, kettle-cooked chips? Done. Hankering for jerky that packs a punch? We've got you covered. Our machines are like treasure chests, waiting for you to unlock flavor magic</p></div>
  <div class="feat r" style="top:190px"><h4>Quality Meets Convenience</h4><p>Imagine this: You're mid-meeting, and your stomach growls. Fear not! SnackOrbit's machines offer top-notch snacks and beverages. It's like having a mini food festival at your fingertips</p></div>
  <div class="feat r" style="top:400px"><h4>Pandemic-Proof &amp;<br>Recession-Ready</h4><p>Life throws curveballs, but SnackOrbit stands strong. Our vending machines are the unsung heroes of resilience. Rain or shine, they're there, serving up joy</p></div>
</section>

<section class="clients">
  <h2 class="serif">What Our Clients Say</h2>
  <div class="arrow" style="left:85px;top:252px;border:1.5px solid #cfd9cd"><svg width="18" height="18" viewBox="0 0 24 24" fill="none" stroke="#fff" stroke-width="2"><path d="M19 12H5M11 6l-6 6 6 6"/></svg></div>
  <div class="arrow" style="left:1080px;top:238px;background:var(--purple)"><svg width="18" height="18" viewBox="0 0 24 24" fill="none" stroke="#fff" stroke-width="2"><path d="M5 12h14M13 6l6 6-6 6"/></svg></div>
  <div class="card" style="left:142px"><span class="q open">“</span><p>Lorem ipsum dolor sit amet, consectetur adipiscing elit. Maecenas pretium tortor, non consectetur nulla. Aenean dignissim sit amet metus at pretium. Integer sed lectus vel velit accumsan semper euac...</p><span class="q close">”</span></div>
  <div class="card" style="left:615px"><span class="q open">“</span><p>Lorem ipsum dolor sit amet, consectetur adipiscing elit. Maecenas pretium tortor, non consectetur nulla. Aenean dignissim sit amet metus at pretium. Integer sed lectus vel velit accumsan semper euac...</p><span class="q close">”</span></div>
</section>
<div class="person" style="left:196px"><span class="avatar" role="img" aria-label="Client portrait photo"></span>Mara Colton</div>
<div class="person" style="left:668px"><span class="avatar" role="img" aria-label="Client portrait photo"></span>Dana Reyes</div>

<section class="cta">
  <h2 class="serif">Ready To Experience The<br><span class="hl">SnackOrbit</span> Difference?</h2>
  <p>Sign up now and let's connect. Taste the future of snacking firsthand! Contact us today<br>and explore how our vending magic can elevate your space.</p>
  <a class="btn btn-green">Contact Us</a>
</section>

<footer class="site-footer">
  <div class="links"><h5>Quick Links</h5><ul><li>Home</li><li>About Us</li><li>Why Choose SnackOrbit</li><li>Product and Services</li><li>Contact Us</li></ul></div>
  <div class="brand"><span class="dot"></span>SnackOrbit</div>
  <div class="social"><span></span><span></span><span></span><span></span></div>
  <div class="contact">
    <h5>Contact Details</h5>
    <div class="row"><svg width="24" height="24" viewBox="0 0 24 24" fill="none" stroke="#fff" stroke-width="1.3"><circle cx="12" cy="12" r="9"/><path d="M3 12h18M12 3c3 3 3 15 0 18M12 3c-3 3-3 15 0 18"/></svg><span>123, Building Name, Street<br>City, State XY 123456</span></div>
    <div class="row"><svg width="24" height="24" viewBox="0 0 24 24" fill="none" stroke="#fff" stroke-width="1.3"><path d="M5 3h4l2 5-2.5 1.5a11 11 0 0 0 6 6L16 13l5 2v4a2 2 0 0 1-2 2A16 16 0 0 1 3 5a2 2 0 0 1 2-2z"/></svg><span>PHONE<br>123-456-7890</span></div>
    <div class="row"><svg width="24" height="24" viewBox="0 0 24 24" fill="none" stroke="#fff" stroke-width="1.3"><rect x="3" y="5" width="18" height="14"/><path d="M3 5l9 8 9-8"/></svg><span>EMAIL<br>info@snackorbit.com</span></div>
  </div>
  <div class="bottom-bar">© 2024 SnackOrbit. all rights reserved.</div>
</footer>

</body>
</html>
```